Business card for my new company (Accounting firm)

I need a business card for my new business Brightwell Advisory and Ledger SA. Our services are accounting, tax, audit and financial management. Our customers are small companies, start-ups and new companies. The final design has to show financial security, trust and growth. Please find our logo attached to the business card. Text for the business card: Brightwell Advisory and Ledger SA Tomas Varenholt Director and Founder Certified Accountant Tel. 022 418 57 34 tv@clairevalconseil.ch www.clairevalconseil.ch Rue des Vergières 27 1201 Geneva
Target Market(s)
Our customers are small companies, start-ups and new companies.
Industry/Entity Type
Finance And Accounting
Contact Information for Business Card
Claireval Conseil et Comptes SA
Tomas Varenholt
Directeur et Fondateur
Expert-comptable diplômé
Tél. 022 418 57 34
tv@clairevalconseil.ch
www.clairevalconseil.ch
Rue des Vergières 27
1201 Genève

```html
<!DOCTYPE html>
<html lang="fr">
<head>
<meta charset="utf-8">
<title>Claireval Conseil et Comptes – Carte de visite</title>
<link href="https://fonts.googleapis.com/css2?family=Roboto:wght@400;500;700&display=swap" rel="stylesheet">
<style>
  :root {
    --bg: #e4e5e7;
    --blue-light: #2fa6da;
    --blue-mid: #2486c0;
    --blue-deep: #1b6aa0;
    --ink-blue: #1d5f98;
    --ink: #3b3f44;
    --ink-soft: #555a60;
    --paper: #f7f7f7;
    --white: #ffffff;
  }
  * { box-sizing: border-box; margin: 0; padding: 0; }
  html, body {
    width: 1200px; height: 726px; overflow: hidden;
    background: var(--bg);
    font-family: "Roboto", Arial, sans-serif;
  }
  .stage {
    position: relative; width: 1200px; height: 726px;
    display: flex; align-items: center; justify-content: center; gap: 60px;
  }
  .card {
    position: relative; width: 520px; height: 297px;
    border-radius: 4px; overflow: hidden;
    box-shadow: 0 6px 18px rgba(0,0,0,0.12);
  }

  /* Front */
  .card-front {
    background: linear-gradient(160deg, var(--blue-light) 0%, var(--blue-mid) 55%, var(--blue-deep) 100%);
    color: var(--white);
    display: flex; flex-direction: column; align-items: center; justify-content: center;
  }
  .front-brand { display: flex; align-items: center; gap: 14px; }
  .brand-square { width: 22px; height: 22px; background: var(--white); }
  .front-brand-name {
    font-weight: 500; font-size: 26px; letter-spacing: 3px;
    text-transform: uppercase; color: var(--white);
  }
  .front-url {
    margin-top: 44px; font-size: 15px; font-weight: 500; letter-spacing: 0.5px;
  }

  /* Back */
  .card-back { background: var(--paper); color: var(--ink); }
  .back-brand {
    position: absolute; top: 56px; right: 34px;
    font-weight: 500; font-size: 19px; letter-spacing: 1.5px;
    text-transform: uppercase; color: var(--ink-blue);
    text-align: right;
  }
  .back-rule {
    position: absolute; top: 90px; right: 34px; width: 230px; height: 1px;
    background: var(--ink-blue);
  }
  .address {
    position: absolute; top: 108px; right: 34px; text-align: right;
    font-size: 13px; line-height: 18px; color: var(--ink);
  }
  .swoosh { position: absolute; left: 0; top: 0; pointer-events: none; }
  .person { position: absolute; left: 34px; top: 148px; }
  .person-name { font-weight: 700; font-size: 19px; line-height: 24px; color: var(--ink-blue); }
  .person-role {
    margin-top: 6px; font-size: 12px; line-height: 15px; color: var(--ink-soft);
  }
  .contacts {
    position: absolute; left: 34px; top: 218px;
    list-style: none; font-size: 13px; line-height: 19px; color: var(--ink);
  }
  .contacts li { display: flex; align-items: center; gap: 10px; }
  .contacts svg { width: 12px; height: 12px; fill: var(--ink-blue); flex: none; }
</style>
</head>
<body>
<main class="stage">

  <section class="card card-front" aria-label="Recto de la carte">
    <div class="front-brand">
      <span class="brand-square"></span>
      <span class="front-brand-name">Claireval</span>
    </div>
    <p class="front-url">www.clairevalconseil.ch</p>
  </section>

  <section class="card card-back" aria-label="Verso de la carte">
    <svg class="swoosh" width="520" height="297" viewBox="0 0 520 297">
      <path d="M190 162 C 240 162, 270 150, 300 140 S 335 130, 350 130" fill="none" stroke="var(--ink-blue)" stroke-width="1"/>
    </svg>

    <p class="back-brand">Claireval</p>
    <div class="back-rule"></div>
    <p class="address">Rue des Vergières 27<br>1201 Genève</p>

    <div class="person">
      <h1 class="person-name">Tomas Varenholt</h1>
      <p class="person-role">Directeur et Fondateur<br>Expert-comptable diplômé</p>
    </div>

    <ul class="contacts">
      <li>
        <svg viewBox="0 0 12 12"><path d="M1 4c0-1.2 1.5-2.5 5-2.5S11 2.8 11 4v1H8.5V3.8h-5V5H1z M3 6h6l1.5 4.5h-9z"/></svg>
        022 418 57 34
      </li>
      <li>
        <svg viewBox="0 0 12 12"><path d="M0.5 2.5h11v7h-11z M1 3l5 3.5L11 3" stroke="var(--paper)" stroke-width="0.8"/></svg>
        tv@clairevalconseil.ch
      </li>
      <li>
        <svg viewBox="0 0 12 12"><circle cx="6" cy="6" r="5.5"/><path d="M0.5 6h11M6 0.5c-2.2 2.8-2.2 8.2 0 11M6 0.5c2.2 2.8 2.2 8.2 0 11" fill="none" stroke="var(--paper)" stroke-width="0.7"/></svg>
        www.clairevalconseil.ch
      </li>
    </ul>
  </section>

</main>
</body>
</html>
```